Orvane Mechanical - Letterhead

We are a plumbing and hvac company based in Calgary. This letterhead will be on our quotes, invoices, preventative maintenance proposals etc.

```html
<!DOCTYPE html>
<html lang="en">
<head>
<meta charset="utf-8">
<title>Orvane Mechanical – Letterhead</title>
<link href="https://fonts.googleapis.com/css2?family=Source+Sans+3:wght@400;600;700&family=Arimo:wght@700&display=swap" rel="stylesheet">
<style>
  :root{
    --backdrop:#d9d9db;
    --paper:#fbfbfb;
    --ink:#3a3a3a;
    --ink-dark:#1c1c1c;
    --brand-blue:#2f6fb7;
    --brand-orange:#e4541f;
    --muted:#555;
  }
  *{box-sizing:border-box;margin:0;padding:0}
  html,body{width:1200px;height:945px;overflow:hidden;background:var(--backdrop)}
  .canvas{position:relative;width:1200px;height:945px}
  .letterhead{
    position:absolute;left:280px;top:20px;width:640px;height:905px;
    background:var(--paper);box-shadow:0 6px 18px rgba(0,0,0,.18);
    font-family:"Source Sans 3",sans-serif;color:var(--ink);overflow:hidden;
  }
  .brand{position:absolute;left:52px;top:70px;display:flex;align-items:center;gap:10px}
  .brand-dot{width:26px;height:26px;border-radius:50%;background:var(--brand-orange)}
  .brand-name{font-weight:700;font-size:24px;color:var(--brand-blue);letter-spacing:.3px}
  .contact{position:absolute;left:430px;top:58px;font-size:10px;line-height:1.4;color:var(--muted)}
  .contact-row{display:flex;align-items:center;gap:5px}
  .contact-row svg{width:8px;height:8px;flex:none}
  .contact-address{padding-left:13px;margin-top:2px}
  .letter-body{position:absolute;left:52px;top:190px;width:530px}
  .salutation{font-family:"Arimo",sans-serif;font-weight:700;font-size:14px;color:var(--ink-dark);margin-bottom:8px}
  .letter-body p{font-size:13px;line-height:1.38;margin-bottom:16px}
  .signature{position:absolute;left:60px;top:640px;width:130px;height:46px;
    background:linear-gradient(90deg,#e6e6e6,#f1f1f1);border-radius:4px}
  .footer{position:absolute;left:0;bottom:0;width:640px;height:80px}
  .footer-url{position:absolute;right:22px;bottom:24px;font-size:10.5px;color:#fff}
</style>
</head>
<body>
<div class="canvas">
  <article class="letterhead">
    <header>
      <div class="brand">
        <span class="brand-dot"></span>
        <span class="brand-name">Orvane Mechanical</span>
      </div>
      <address class="contact" style="font-style:normal">
        <div class="contact-row">
          <svg viewBox="0 0 10 10"><path d="M2 1l2 2-1 1.2c.6 1.2 1.6 2.2 2.8 2.8L7 6l2 2-1.4 1.4C4.5 9 1 5.5.6 2.4z" fill="var(--brand-orange)"/></svg>
          855-010-4821
        </div>
        <div class="contact-row">
          <svg viewBox="0 0 10 10"><rect x="0.5" y="2" width="9" height="6.5" rx="1" fill="var(--brand-orange)"/><path d="M1 2.5l4 3 4-3" stroke="#fff" stroke-width="1" fill="none"/></svg>
          info@orvanemechanical.com
        </div>
        <div class="contact-address">Po. Box 56, Street Name,<br>City Name, Zip Code - 00000</div>
      </address>
    </header>

    <section class="letter-body">
      <div class="salutation">Dear Mr. John,</div>
      <p>Lorem Ipsum is simply dummy text of the printing and typesetting industry. Lorem Ipsum has been the industry's standard dummy text ever since the 1500s, when an unknown printer took a galley of type and scrambled it to make a type specimen book. It has survived not only five centuries, but also the leap into electronic typesetting, remaining essentially unchanged.</p>
      <p>The standard chunk of Lorem Ipsum used since the 1500s is reproduced below for those interested. Sections 1.10.32 and 1.10.33 from "de Finibus Bonorum et Malorum" by Cicero are also reproduced in their exact original form, accompanied by English versions from the 1914 translation by H. Rackham</p>
      <p>Lorem Ipsum is simply dummy text of the printing and typesetting industry. Lorem Ipsum has been the industry's standard dummy text ever since the 1500s, when an unknown printer took a galley of type and scrambled it to make a type specimen book. It has survived not only five centuries, but also the leap into electronic typesetting, remaining essentially unchanged. It was popularised in the</p>
      <p>The standard chunk of Lorem Ipsum used since the 1500s is reproduced below for those interested. Sections 1.10.32 and 1.10.33 from "de Finibus Bonorum et Malorum" by Cicero are also reproduced in their exact original form, accompanied by English versions from the 1914 translation by H. Rackham</p>
      <p>The standard chunk of Lorem Ipsum used since the 1500s is reproduced below for those interested. Sections 1.10.32 and 1.10.33 from "de Finibus Bonorum et Malorum" by Cicero are also reproduced in their exact original form.</p>
    </section>

    <div class="signature" role="img" aria-label="Handwritten signature of the sender"></div>

    <footer class="footer">
      <svg width="640" height="80" viewBox="0 0 640 80">
        <path d="M0 66 H400 Q412 66 418 56 L426 42 Q432 32 444 32 H640 V40 H446 Q436 40 431 49 L423 63 Q416 74 402 74 H0 Z" fill="var(--brand-orange)"/>
        <path d="M0 71 H404 Q418 71 425 58 L432 46 Q437 38 448 38 H640 V80 H0 Z" fill="var(--brand-blue)"/>
        <rect x="0" y="74" width="640" height="6" fill="var(--paper)"/>
        <rect x="0" y="74" width="640" height="3" fill="var(--brand-blue)"/>
      </svg>
      <span class="footer-url">www.orvanemechanical.com</span>
    </footer>
  </article>
</div>
</body>
</html>
```